Business card design for sustainable building and development company

Need a business card design for a new sustainable building and real estate development company in the San Francisco Bay area. Name of company is "Tovrin Advisors, LLC" and we provide "Sustainable building, energy and development services" for residential and non residential projects. We'd like the following colors used but not all area required: green, gray, blue. Design should communicate innovation, professionalism and sustainability. Our current website is www.tovrin-advisors.example. Another possible design idea is to have the following listed on the back of the card:
Certified: VERN QS, Eco Marker Rater, DOLM Rater, Terravue Inspector, KSO TQ Building Analyst. Its not a must but could be text that could be used for back of card. Overall, we are open to a simple, clean design and or one with more text than usual for a card.

Industry/Entity Type

Real Estate

Contact Information for Business Card

Name on card: Mark J. Halvik
Title for Name: Principal + Founder
Phone: 555.814.0627
Email: mhalvik@tovrin-advisors.example
Website: www.tovrin-advisors.example

Also, please add the following for address:
Harlen Bay, Verdania

Requirements
Nice to have
• If you can integrate the outline of a skyline on the backside of the card and if it looks good, I would like to see the design
Should not have
• a barcode;

```html
<!DOCTYPE html>
<html lang="en">
<head>
<meta charset="utf-8">
<title>Tovrin Advisors — Business Card</title>
<link rel="stylesheet" href="https://fonts.googleapis.com/css2?family=Roboto:wght@400;500;700&display=swap">
<style>
  :root {
    --bg: #5c5d5f;
    --green: #63b33e;
    --green-dark: #4c8f2c;
    --paper: #f4f4f2;
    --ink: #3b3b3b;
    --white: #ffffff;
  }
  html, body { margin: 0; padding: 0; overflow: hidden; }
  body {
    width: 1200px; height: 1029px;
    background: var(--bg);
    font-family: "Roboto", Arial, sans-serif;
    position: relative;
  }
  .card {
    position: absolute;
    left: 220px;
    width: 760px; height: 434px;
    background: var(--green);
    box-shadow: 0 10px 28px rgba(0,0,0,.35);
    overflow: hidden;
  }
  .card--back { top: 48px; }
  .card--front { top: 547px; }

  /* Back */
  .back-band {
    position: absolute; left: 0; right: 0;
    top: 96px; height: 104px;
    background: var(--paper);
  }
  .brand {
    position: absolute; display: flex; align-items: center; gap: 14px;
  }
  .brand-dot {
    border-radius: 50%; background: var(--green); flex: none;
  }
  .brand-text { display: flex; flex-direction: column; }
  .brand-name {
    color: var(--green); font-weight: 700; line-height: 1; white-space: nowrap;
  }
  .brand-tagline {
    color: var(--ink); text-transform: uppercase; font-weight: 500;
    letter-spacing: .02em; white-space: nowrap; margin-top: 4px;
  }
  .card--back .brand { left: 150px; top: 110px; }
  .card--back .brand-dot { width: 76px; height: 76px; }
  .card--back .brand-name { font-size: 44px; }
  .card--back .brand-tagline { font-size: 11.5px; }
  .back-url {
    position: absolute; left: 0; right: 0; top: 262px; margin: 0;
    text-align: center; color: var(--white);
    font-size: 14px; letter-spacing: .16em; text-transform: uppercase;
  }

  /* Front */
  .front-band {
    position: absolute; left: 0; top: 30px;
    width: 470px; height: 106px;
    background: var(--paper);
  }
  .card--front .brand { left: 22px; top: 45px; }
  .card--front .brand-dot { width: 70px; height: 70px; }
  .card--front .brand-name { font-size: 33px; }
  .card--front .brand-tagline { font-size: 9px; }
  .person { position: absolute; left: 44px; top: 166px; }
  .person-name {
    color: var(--paper); font-size: 23px; font-weight: 700;
    letter-spacing: .12em; text-transform: uppercase; margin: 0;
  }
  .person-title {
    color: var(--green-dark); font-size: 14px; font-weight: 500;
    letter-spacing: .1em; text-transform: uppercase; margin: 2px 0 0;
  }
  .contact {
    position: absolute; list-style: none; margin: 0; padding: 0;
    color: var(--white); font-size: 14px; letter-spacing: .12em;
    text-transform: uppercase;
  }
  .contact li { display: flex; align-items: center; gap: 16px; height: 30px; }
  .contact svg { width: 15px; height: 15px; flex: none; }
  .contact--personal { left: 44px; top: 246px; }
  .contact--company { left: 432px; top: 330px; }
</style>
</head>
<body>

<section class="card card--back" aria-label="Card back">
  <div class="back-band"></div>
  <div class="brand">
    <span class="brand-dot"></span>
    <div class="brand-text">
      <span class="brand-name">Tovrin Advisors</span>
      <span class="brand-tagline">Green Building, Power &amp; Land Planning Services</span>
    </div>
  </div>
  <p class="back-url">www.tovrin-advisors.example</p>
</section>

<section class="card card--front" aria-label="Card front">
  <div class="front-band"></div>
  <div class="brand">
    <span class="brand-dot"></span>
    <div class="brand-text">
      <span class="brand-name">Tovrin Advisors</span>
      <span class="brand-tagline">Green Building, Power &amp; Land Planning Services</span>
    </div>
  </div>

  <div class="person">
    <h1 class="person-name">Mark J. Halvik</h1>
    <p class="person-title">Principal/Owner</p>
  </div>

  <ul class="contact contact--personal">
    <li>
      <svg viewBox="0 0 16 16" aria-hidden="true"><rect x="4" y="1" width="8" height="14" rx="1.5" fill="none" stroke="#fff" stroke-width="1.4"/><circle cx="8" cy="12.5" r=".9" fill="#fff"/></svg>
      <span>555.814.0627</span>
    </li>
    <li>
      <svg viewBox="0 0 16 16" aria-hidden="true"><rect x="1" y="3" width="14" height="10" fill="#fff"/><path d="M1 3 L8 9 L15 3" fill="none" stroke="#63b33e" stroke-width="1.3"/></svg>
      <span>mhalvik@tovrin-advisors.example</span>
    </li>
  </ul>

  <ul class="contact contact--company">
    <li>
      <svg viewBox="0 0 16 16" aria-hidden="true"><circle cx="8" cy="8" r="6.5" fill="none" stroke="#fff" stroke-width="1.4"/><ellipse cx="8" cy="8" rx="2.8" ry="6.5" fill="none" stroke="#fff" stroke-width="1.1"/><path d="M1.5 8 H14.5" stroke="#fff" stroke-width="1.1"/></svg>
      <span>www.tovrin-advisors.example</span>
    </li>
    <li>
      <svg viewBox="0 0 16 16" aria-hidden="true"><path d="M8 15 C4 10 3 8 3 6 A5 5 0 0 1 13 6 C13 8 12 10 8 15 Z" fill="#fff"/><circle cx="8" cy="6" r="1.8" fill="#63b33e"/></svg>
      <span>Harlen Bay, Verdania</span>
    </li>
  </ul>
</section>

</body>
</html>
```